Business card design for new eCommerce site focusing on integrity and strong businsess tactics

We need a business card that will stand out and be memorable. Something with color that matches our company logo colors. Think high end version of Pactivo. There are 2 logos provided. The parent company is called Amber Ledge Partners and we are presenting a new and very exciting eCommerce site called BrightHarborTrade.example.

Target Market(s)

Our target markets are in the Activities, Food and Beverage, Health and Beauty

Industry/Entity Type

Marketing

Contact Information for Business Card

We have 4 members that need cards...I will provide all info to the winner of the design contest
Business Address is
4870 West 63rd Avenue, Suite C207
Phoenix AZ 85731

Font styles to use
Serif
Sans Serif

Colors

Designer to choose colors to be used in the design.

Requirements
Must have
• The card must be memorable...should be unique in design but must exude integrity and be playful .
• I have provided several colors or our parent company...please feel free to use which ever
Nice to have
• I will leave this up to you. Feel free to use other images of your choosing that wraps around our client.....Activities, Dining, Health, Beauty
Should not have
• just dont be boring

```html
<!DOCTYPE html>
<html lang="en">
<head>
<meta charset="utf-8">
<title>Business Card – BrightHarborTrade.example</title>
<link rel="stylesheet" href="https://fonts.googleapis.com/css2?family=Jost:wght@400;500;700&display=swap">
<style>
  :root {
    --page: #2a2a2a;
    --blue-light: #44b8d8;
    --blue: #2f86bd;
    --blue-deep: #2a7ab2;
    --green: #8cc63f;
    --green-light: #b8e04e;
    --green-deep: #74bf30;
    --paper: #f4f4f4;
    --navy: #10194a;
    --grey-text: #555;
    --white: #ffffff;
  }
  * { margin: 0; padding: 0; box-sizing: border-box; }
  html, body { width: 1200px; height: 960px; overflow: hidden; }
  body {
    background: var(--page);
    position: relative;
    font-family: "Jost", sans-serif;
  }
  .card {
    position: absolute;
    width: 600px;
    height: 343px;
    border-radius: 22px;
    overflow: hidden;
  }
  .card-front { left: 302px; top: 130px; background: var(--paper); }
  .card-back {
    left: 299px; top: 490px; height: 342px;
    background: linear-gradient(135deg, var(--green-light) 0%, var(--green-deep) 45%, var(--green-deep) 100%);
  }
  .front-art { position: absolute; inset: 0; }

  .contact-block { position: absolute; left: 28px; top: 72px; color: var(--white); }
  .person-name { color: var(--green); font-weight: 500; font-size: 23px; line-height: 1; letter-spacing: 0.3px; }
  .person-title { font-size: 14px; margin-top: 5px; letter-spacing: 0.3px; }
  .address { font-size: 14px; line-height: 18px; margin-top: 14px; }
  .contact-list { list-style: none; margin-top: 14px; font-size: 14px; }
  .contact-list li { display: flex; align-items: center; height: 19.5px; }
  .contact-icon { width: 12px; height: 12px; margin-right: 9px; fill: var(--green); flex: none; }

  .brand-front { position: absolute; left: 312px; top: 152px; }
  .brand-row { display: flex; align-items: center; }
  .brand-dot { width: 16px; height: 16px; border-radius: 50%; background: var(--green); margin-right: 8px; }
  .brand-name { color: var(--blue); font-weight: 500; font-size: 21px; line-height: 1; }
  .brand-tagline { color: var(--grey-text); font-size: 11px; letter-spacing: 0.6px; margin-top: 4px; padding-left: 24px; }

  .brand-back { position: absolute; left: 0; right: 0; top: 70px; text-align: center; }
  .brand-back-circle {
    width: 122px; height: 122px; margin: 0 auto;
    border-radius: 50%; background: var(--navy);
    box-shadow: 0 0 0 3px var(--green-deep), 0 0 0 4px var(--navy);
  }
  .brand-back-name { color: var(--navy); font-weight: 700; font-size: 33px; margin-top: 20px; line-height: 1; }
</style>
</head>
<body>

<section class="card card-front" aria-label="Card front">
  <svg class="front-art" viewBox="0 0 600 343" preserveAspectRatio="none" aria-hidden="true">
    <defs>
      <linearGradient id="panelBlue" x1="0" y1="0" x2="1" y2="1">
        <stop offset="0" stop-color="#44b8d8"/>
        <stop offset="0.55" stop-color="#2f86bd"/>
        <stop offset="1" stop-color="#2a7ab2"/>
      </linearGradient>
    </defs>
    <path d="M0 0 H295 C240 40 210 120 245 205 C272 265 305 300 300 343 H0 Z" fill="url(#panelBlue)"/>
    <path d="M280 0 C235 40 215 115 245 195 C262 240 290 280 292 343" fill="none" stroke="#ffffff" stroke-width="9"/>
    <path d="M300 0 C250 40 225 120 258 200 C282 255 318 300 306 343" fill="none" stroke="#2f86bd" stroke-width="5"/>
    <path d="M290 6 C255 35 238 80 245 130" fill="none" stroke="#8cc63f" stroke-width="4"/>
    <path d="M268 190 C290 240 300 285 288 343" fill="none" stroke="#8cc63f" stroke-width="4"/>
  </svg>

  <div class="contact-block">
    <h1 class="person-name">DANA WHITFIELD</h1>
    <p class="person-title">CEO/FOUNDER</p>
    <p class="address">4870 West 63rd Avenue<br>Suite C207<br>Phoenix AZ 85731</p>
    <ul class="contact-list">
      <li><svg class="contact-icon" viewBox="0 0 12 12"><path d="M2.5 0.5 L4.5 0.5 L5.3 3.2 L3.9 4.3 C4.5 5.8 6.2 7.5 7.7 8.1 L8.8 6.7 L11.5 7.5 L11.5 9.5 C11.5 10.6 10.6 11.5 9.5 11.5 C4.5 11.2 0.8 7.5 0.5 2.5 C0.5 1.4 1.4 0.5 2.5 0.5 Z"/></svg>602 555 0148</li>
      <li><svg class="contact-icon" viewBox="0 0 12 12"><path d="M3 0 H9 A1 1 0 0 1 10 1 V11 A1 1 0 0 1 9 12 H3 A1 1 0 0 1 2 11 V1 A1 1 0 0 1 3 0 Z M3.5 1.5 V9.5 H8.5 V1.5 Z"/></svg>602 555 0193</li>
      <li><svg class="contact-icon" viewBox="0 0 12 12"><path d="M0 2 H12 V10 H0 Z M1 3 L6 6.5 L11 3 Z" fill-rule="evenodd"/></svg>dana@brightharbortrade.example</li>
      <li><svg class="contact-icon" viewBox="0 0 12 12"><path d="M6 0 A6 6 0 1 0 6 12 A6 6 0 1 0 6 0 Z M2 4 C3 3 4 4 5 3.5 C5.5 5 4 6 3 6.5 C2.5 7.5 3 9 2.2 9 C1.2 7.5 1.2 5.5 2 4 Z M7 2 C8.5 2.5 10 3.5 10.5 5 C9 5 8.5 6 9 7.5 C8 8 7 7 7.5 5.5 C7 4.5 6.5 3 7 2 Z"/></svg>www.brightharbortrade.example</li>
    </ul>
  </div>

  <div class="brand-front">
    <div class="brand-row">
      <span class="brand-dot"></span>
      <span class="brand-name">BrightHarborTrade.example</span>
    </div>
    <p class="brand-tagline">Activities-Dining-Health-Beauty</p>
  </div>
</section>

<section class="card card-back" aria-label="Card back">
  <div class="brand-back">
    <div class="brand-back-circle"></div>
    <p class="brand-back-name">Amber Ledge Partners</p>
  </div>
</section>

</body>
</html>
```